Business Cards Design for the electrical wholesaler: clean bold dynamic :)

We need a business card design that would follow our latest brand guidelines. As an electrical wholesaler we want to bring a fresh look and feel into the industry. The design should be clean bold and dynamic. It should come alive with the renewed energy of our green colour. Our grey colour should keep things balanced and complement the notion of maturity and responsibility. We employ Lato as a corporate font however are not bound by this font and we’re open to interpretation here.

Target Market(s)

Electrical contractors

Industry/Entity Type

Business

Contact Information for Business Card

Logo
Name & Surname: Halyna Dorosh
Job Title: Director of Marketing
Email: halya.dorosh@quillmail.example
Cell phone: XXX.XXX.XXXX
Address: 20517 - 87 Ave. Edmonton, AB, Canada. T6K 4N8
Business Phone: 780.555.0184
Website: www.brovix.example

Font styles to use
Other font styles liked:
• Lato

Requirements
Must have
• Logo & website
Nice to have
• Brand elements - some of them you may find in the attached Brand Guidelines (e.g. three lines on the background signifying "W")

```html
<!DOCTYPE html>
<html lang="en">
<head>
<meta charset="utf-8">
<title>Brovix Business Card</title>
<link rel="stylesheet" href="https://fonts.googleapis.com/css2?family=Lato:wght@400;700;900&display=swap">
<style>
  :root {
    --backdrop: #3a3a3c;
    --card-black: #1e1e20;
    --card-dark: #262628;
    --gloss: #2f2f31;
    --brand-green: #7fc31c;
    --brand-grey: #b3b3b5;
    --ink-white: #f2f2f2;
  }
  * { margin: 0; padding: 0; box-sizing: border-box; }
  html, body {
    width: 799px; height: 1200px; overflow: hidden;
    background: var(--backdrop);
    font-family: "Lato", sans-serif;
  }
  .sheet { position: relative; width: 799px; height: 1200px; }
  .card {
    position: absolute; left: 90px; width: 620px; height: 354px;
    border-radius: 22px; overflow: hidden;
    box-shadow: 0 14px 30px rgba(0,0,0,.45);
  }
  .card--front { top: 100px; background: var(--card-black); }
  .card--back { top: 700px; background: var(--card-dark); }

  .brand { position: absolute; display: flex; align-items: center; gap: 14px; }
  .brand__mark { width: 32px; height: 32px; border-radius: 4px; }
  .brand__name { font-weight: 900; letter-spacing: 1px; }

  .card--front .brand { left: 150px; top: 130px; }
  .card--front .brand__mark { background: var(--gloss); width: 52px; height: 52px; }
  .card--front .brand__name { color: var(--gloss); font-size: 76px; line-height: 1; }

  .card--back .brand { left: 36px; top: 30px; }
  .card--back .brand__mark { background: var(--brand-green); }
  .card--back .brand__name { color: var(--ink-white); font-size: 48px; line-height: 1; }

  .person { position: absolute; left: 38px; top: 100px; }
  .person__name { color: var(--brand-green); font-weight: 700; font-size: 26px; line-height: 1.2; }
  .person__title { color: var(--ink-white); font-size: 13px; margin-top: 2px; }

  .waves { position: absolute; left: 0; top: 0; width: 620px; height: 354px; }

  .contact {
    position: absolute; right: 30px; bottom: 18px;
    list-style: none; text-align: right;
    color: var(--ink-white); font-size: 14px; line-height: 19px;
  }
  .contact li { display: flex; justify-content: flex-end; align-items: center; gap: 8px; }
  .contact svg { width: 13px; height: 13px; flex: none; }
  .contact .no-icon { padding-right: 21px; }
</style>
</head>
<body>
<main class="sheet">
  <section class="card card--front" aria-label="Card front">
    <div class="brand">
      <span class="brand__mark"></span>
      <span class="brand__name">Brovix</span>
    </div>
  </section>

  <section class="card card--back" aria-label="Card back">
    <svg class="waves" viewBox="0 0 620 354" aria-hidden="true">
      <path d="M0 170 C120 150 220 220 330 217 C430 214 540 150 620 125 L620 137 C540 162 430 226 330 229 C220 232 120 162 0 182 Z" fill="#b3b3b5"/>
      <path d="M0 195 C120 175 220 245 330 242 C430 239 540 175 620 150 L620 354 L0 354 Z" fill="#7fc31c"/>
    </svg>
    <div class="brand">
      <span class="brand__mark"></span>
      <span class="brand__name">Brovix</span>
    </div>
    <div class="person">
      <p class="person__name">Halyna Dorosh</p>
      <p class="person__title">Director of Marketing</p>
    </div>
    <ul class="contact">
      <li class="no-icon">www.brovix.example</li>
      <li>halya.dorosh@quillmail.example
        <svg viewBox="0 0 14 14"><circle cx="7" cy="7" r="6" fill="none" stroke="#f2f2f2"/><rect x="4" y="5" width="6" height="4" fill="none" stroke="#f2f2f2" stroke-width=".8"/></svg></li>
      <li>Cell XXX.XXX.XXXX
        <svg viewBox="0 0 14 14"><circle cx="7" cy="7" r="6" fill="none" stroke="#f2f2f2"/><rect x="5" y="3.5" width="4" height="7" rx=".8" fill="none" stroke="#f2f2f2" stroke-width=".9"/></svg></li>
      <li>Office 780.555.0184
        <svg viewBox="0 0 14 14"><circle cx="7" cy="7" r="6" fill="none" stroke="#f2f2f2"/><path d="M4.5 5c0 3 2 4.5 4.5 4.5l.5-1.2-1.3-.6-.5.5c-.8-.3-1.4-.9-1.7-1.7l.5-.5L6 4.7z" fill="#f2f2f2"/></svg></li>
      <li>20517 - 87 Ave. Edmonton,
        <svg viewBox="0 0 14 14"><circle cx="7" cy="7" r="6" fill="none" stroke="#f2f2f2"/><path d="M7 3.5a2 2 0 0 1 2 2c0 1.6-2 4-2 4s-2-2.4-2-4a2 2 0 0 1 2-2z" fill="#f2f2f2"/></svg></li>
      <li class="no-icon">AB, Canada. T6K 4N8</li>
    </ul>
  </section>
</main>
</body>
</html>
```